New label design for Vitmain Water beverage

This is to create a new label for a vitamin water company called Qirna Vitamin. The label should be in dual languages. English and Arabic as seen attached for a previous example. You do not have to create an Arabic logo, just make space for it and I will have someon else do it. If you think you can do it, go ahead. I have also attached the bottle dimensions we are thinking of using. Please provide a new bottle design if you see fit. Please remember the bottle size is 400ml, and no pressure If I don't get a great bottle design, then I will use the attached one in that case. Please make the label diverse for various flavors, so it would apply easily and color print friendly. The brand is healthy, sporty, low or no sugars, no artificial flavors and no artificial coloring. All vitamins, minirals and electrolytes are healthy and real. Three flavors: pomogranite cherry, tropical citrus, and kiwi strawberry. So, each label would have different vitamins and offers unique components. Make it hip, trendy yet classy.
Good Luck!!!
Updates

Project Deadline Extended Reason: Because I updated a new file image example to follow and innovate from. Added Monday, February 02, 2015

Posted new file image example to follow and innovate from. Thanks, Added Monday, February 02, 2015

Target Market(s)

Age 15-40 males and females

Industry/Entity Type

Water Company

Requirements
Nice to have
• Plastic PET bottle design
• a 500 ml version

```html
<!DOCTYPE html>
<html lang="en">
<head>
<meta charset="utf-8">
<title>Qirna Vitamin – Pomogranite Cherry Label</title>
<link rel="stylesheet" href="https://fonts.googleapis.com/css2?family=PT+Sans+Narrow:wght@400;700&family=Open+Sans:wght@400;600;700&family=Cairo:wght@400;700&display=swap">
<style>
  :root {
    --bg: #e9e9e9;
    --bg-deep: #cfcfcf;
    --white: #ffffff;
    --red: #e2363c;
    --red-dark: #8e1b1d;
    --red-soft: #f28a8d;
    --orange: #e27a22;
    --ink: #2b2b2b;
    --grey: #6e6f71;
    --line: #9a9a9a;
    --panel-border: #8d8d8d;
  }
  * { box-sizing: border-box; margin: 0; padding: 0; }
  html, body { width: 1200px; height: 1000px; overflow: hidden; }
  body {
    background: linear-gradient(180deg, #f4f4f4 0%, var(--bg) 60%, #dedede 100%);
    font-family: "Open Sans", Arial, sans-serif;
    color: var(--ink);
    position: relative;
  }

  /* presentation header */
  .sheet-title {
    position: absolute; left: 63px; top: 58px;
    font-family: "PT Sans Narrow", Arial, sans-serif;
    font-weight: 700; font-size: 38px; line-height: 1; color: #111;
  }
  .header-brand { position: absolute; left: 50px; top: 104px; }
  .header-brand .kicker {
    font-family: "PT Sans Narrow", Arial, sans-serif;
    font-size: 24px; letter-spacing: 3px; color: #222; padding-left: 13px;
  }
  .header-brand .name {
    font-family: "PT Sans Narrow", Arial, sans-serif;
    font-weight: 700; font-size: 66px; line-height: 1; color: var(--red);
  }
  .header-brand .flavour {
    font-family: "PT Sans Narrow", Arial, sans-serif;
    font-weight: 700; font-size: 27px; color: var(--grey); margin-top: 6px;
  }

  /* flat label */
  .label {
    position: absolute; left: 25px; top: 305px;
    width: 1150px; height: 670px; overflow: hidden;
  }
  .label-art { position: absolute; inset: 0; }
  .red-band {
    position: absolute; left: 0; top: 615px; width: 100%; height: 55px;
    background: linear-gradient(180deg, #ef5a5e, var(--red));
  }

  .brand-name {
    position: absolute;
    font-family: "PT Sans Narrow", Arial, sans-serif;
    font-weight: 700; color: var(--orange); font-size: 34px; line-height: 1;
  }
  .brand-lockup {
    position: absolute;
    font-family: "PT Sans Narrow", Arial, sans-serif;
    font-weight: 700; color: var(--red-dark); line-height: 1; white-space: nowrap;
  }
  .arabic { font-family: "Cairo", Arial, sans-serif; direction: rtl; }

  .flavour-block { position: absolute; text-align: center; }
  .flavour-block .flavour-name {
    font-family: "PT Sans Narrow", Arial, sans-serif;
    font-weight: 700; font-size: 21px; color: var(--grey);
    border-bottom: 2px solid var(--red-dark); padding-bottom: 1px;
  }
  .flavour-block .claim {
    font-size: 10.5px; letter-spacing: 1.2px; color: var(--grey);
    padding: 3px 0; border-bottom: 1px solid var(--red-soft);
    background: rgba(255,255,255,0.55);
  }
  .flavour-block.arabic .flavour-name { font-family: "Cairo", Arial, sans-serif; font-size: 16px; color: var(--red-dark); }
  .flavour-block.arabic .claim { font-size: 10px; letter-spacing: 0; padding: 1px 0; }

  .calorie-badge {
    position: absolute; width: 50px; height: 50px;
    border: 2px solid var(--red-dark); border-radius: 7px; background: var(--white);
    text-align: center; color: var(--red-dark);
  }
  .calorie-badge .count { font-family: "PT Sans Narrow", Arial, sans-serif; font-weight: 700; font-size: 28px; line-height: 28px; }
  .calorie-badge .unit { font-size: 6.5px; font-weight: 700; line-height: 8px; text-transform: uppercase; }
  .calorie-badge .unit.arabic { font-family: "Cairo", Arial, sans-serif; font-size: 7px; }

  .volume {
    position: absolute; font-family: "Open Sans", Arial, sans-serif;
    font-weight: 700; font-size: 12.5px; color: var(--ink);
  }

  /* nutrition panels */
  .facts-title {
    position: absolute; font-weight: 700; font-size: 13px; color: var(--red-dark);
    font-family: "Open Sans", Arial, sans-serif;
  }
  .facts-title.arabic { font-family: "Cairo", Arial, sans-serif; font-size: 13px; }
  .facts-panel {
    position: absolute; width: 230px; height: 437px;
    background: rgba(255,255,255,0.96);
    border: 1.5px solid var(--panel-border); border-radius: 5px;
    box-shadow: 0 0 4px rgba(0,0,0,0.25);
    padding: 6px 10px; font-size: 8px; line-height: 14.5px; color: #333;
  }
  .facts-panel .row { display: flex; justify-content: space-between; border-bottom: 1px solid #cfcfcf; }
  .facts-panel .row.thick { border-bottom: 3px solid #333; }
  .facts-panel .row.plain { border-bottom: none; }
  .facts-panel .row.right { justify-content: flex-end; font-weight: 700; }
  .facts-panel .vit { display: grid; grid-template-columns: 1fr 52px 52px; border-bottom: 1px solid #cfcfcf; }
  .facts-panel .vit span:not(:first-child) { text-align: right; }
  .facts-panel .vit.head { font-weight: 700; border-bottom: 1.5px solid #333; }
  .facts-panel .note { font-size: 7.5px; padding: 2px 0 4px; border-bottom: 1px solid #cfcfcf; }
  .facts-panel .section { padding: 4px 0; border-bottom: 1px solid #cfcfcf; font-size: 7.5px; line-height: 11px; }
  .facts-panel .section strong { display: block; font-size: 8px; }
  .facts-panel .section p + p { margin-top: 5px; }
  .facts-panel .section em { font-style: italic; display: block; }
  .facts-panel.arabic { font-family: "Cairo", Arial, sans-serif; line-height: 14.5px; }
  .facts-panel.arabic .vit span:not(:first-child) { text-align: left; }
</style>
</head>
<body>

  <h1 class="sheet-title">Label Design</h1>
  <div class="header-brand">
    <div class="kicker">VITAMIN</div>
    <div class="name">Qirna</div>
    <div class="flavour">POMOGRANITE CHERRY</div>
  </div>

  <section class="label" aria-label="Qirna Vitamin Pomogranite Cherry label, flat">
    <svg class="label-art" width="1150" height="670" viewBox="0 0 1150 670" aria-hidden="false">
      <defs>
        <linearGradient id="greyTop" x1="0" y1="0" x2="0" y2="1">
          <stop offset="0" stop-color="#bdbdbd"/>
          <stop offset="1" stop-color="#ececec"/>
        </linearGradient>
        <linearGradient id="splashRed" x1="0" y1="0" x2="1" y2="1">
          <stop offset="0" stop-color="#f6b3b5" stop-opacity="0.6"/>
          <stop offset="0.5" stop-color="#d9262d"/>
          <stop offset="1" stop-color="#f4a1a4" stop-opacity="0.5"/>
        </linearGradient>
        <linearGradient id="splashFade" x1="0" y1="0" x2="0" y2="1">
          <stop offset="0" stop-color="#f7c9ca" stop-opacity="0.5"/>
          <stop offset="1" stop-color="#ffffff" stop-opacity="0"/>
        </linearGradient>
      </defs>
      <rect width="1150" height="670" fill="url(#greyTop)"/>
      <path d="M0,130 C200,40 420,60 575,120 C720,175 860,80 1150,60 L1150,670 L0,670 Z" fill="#dcdcdc"/>
      <path d="M0,175 C200,70 400,95 575,165 C700,200 830,120 1150,95 L1150,670 L0,670 Z" fill="var(--white)"/>
      <g role="img" aria-label="Red pomegranate cherry juice splash with bubbles">
        <path d="M0,300 C110,300 220,390 330,470 L330,530 C220,480 110,440 0,430 Z" fill="url(#splashRed)"/>
        <path d="M0,430 C110,440 220,480 330,530 L330,610 L0,610 Z" fill="url(#splashFade)"/>
      </g>
      <g role="img" aria-label="Red pomegranate cherry juice wave with bubbles">
        <path d="M550,500 C690,300 880,300 1150,250 L1150,430 C950,470 760,470 550,540 Z" fill="url(#splashRed)"/>
        <path d="M550,540 C760,470 950,470 1150,430 L1150,610 L550,610 Z" fill="url(#splashFade)"/>
      </g>
    </svg>

    <div class="red-band"></div>

    <!-- Arabic face -->
    <div class="brand-name" style="left:118px; top:82px;">Qirna</div>
    <div class="brand-lockup arabic" style="left:88px; top:198px; width:170px; text-align:center; font-family:'Cairo',Arial,sans-serif; font-size:22px; color:var(--red);">قرنة فيتامين</div>
    <div class="brand-lockup" style="left:72px; top:238px; width:210px; text-align:center; font-size:44px;">Qirna</div>

    <div class="flavour-block arabic" style="left:93px; top:310px; width:165px;">
      <div class="flavour-name">رمان كرز</div>
      <div class="claim">منكه + نكهة طبيعية</div>
      <div class="claim">بدون ألوان صناعية</div>
      <div class="claim">معادن وأملاح حقيقية</div>
    </div>

    <div class="calorie-badge" style="left:140px; top:520px;">
      <div class="count">50</div>
      <div class="unit arabic">سعرة لكل عبوة</div>
    </div>
    <div class="volume" style="left:47px; top:576px;">500 ML</div>

    <div class="facts-title arabic" style="left:360px; top:58px;">حقائق غذائية</div>
    <div class="facts-panel arabic" style="left:322px; top:88px;">
      <div class="row"><span>حجم الحصة</span><span>500 مل</span></div>
      <div class="row thick"><span>عدد الحصص</span><span>1</span></div>
      <div class="row thick"><span>الكمية لكل حصة</span><span>السعرات 50</span></div>
      <div class="row right"><span>القيمة اليومية %</span></div>
      <div class="row"><span>الدهون</span><span>0g [0%]</span></div>
      <div class="row"><span>الصوديوم</span><span>1.28g [53%]</span></div>
      <div class="row"><span>الكربوهيدرات</span><span>9.6g [3.2%]</span></div>
      <div class="row"><span>السكر</span><span>9.6g</span></div>
      <div class="row thick"><span>البروتين</span><span>0g</span></div>
      <div class="vit head"><span></span><span>لكل حصة</span><span>لكل عبوة</span></div>
      <div class="vit"><span>فيتامين C</span><span>18.3%</span><span>18.3%</span></div>
      <div class="vit"><span>فيتامين E</span><span>3.5%</span><span>3.5%</span></div>
      <div class="vit"><span>فيتامين B3</span><span>3.0%</span><span>3.0%</span></div>
      <div class="vit"><span>فيتامين B5</span><span>3.0%</span><span>3.0%</span></div>
      <div class="vit"><span>فيتامين B6</span><span>5.5%</span><span>5.5%</span></div>
      <div class="vit"><span>فيتامين B12</span><span>2.3%</span><span>2.3%</span></div>
      <div class="vit"><span>كالسيوم</span><span>2.7%</span><span>2.7%</span></div>
      <div class="note">القيمة اليومية على أساس 2000 سعرة</div>
      <div class="section">
        <strong>المكونات</strong>
        ماء منقى، سكر، فركتوز، نكهات، ألوان، حمض غذائي، فيتامينات، لاكتات الكالسيوم
      </div>
      <div class="section">
        <strong>صنع حصريا</strong>
        صنع حصريا لشركة قرنة فيتامين بمكونات مستوردة في ماليزيا
      </div>
      <div class="row plain" style="font-size:7.5px;"><span>للمبيعات والتوزيع: info@qirnavitamin.com</span></div>
    </div>

    <!-- English face -->
    <div class="brand-name" style="left:640px; top:82px;">Qirna</div>
    <div class="brand-lockup" style="left:572px; top:208px; width:260px; text-align:center; font-size:42px;">Qirna Vitamin</div>

    <div class="flavour-block" style="left:598px; top:304px; width:202px;">
      <div class="flavour-name">POMOGRANITE CHERRY</div>
      <div class="claim">Flavoured + Natural Flavour</div>
      <div class="claim">No Artificial Coloring Added</div>
      <div class="claim">Real Minirals &amp; Electrolytes</div>
    </div>

    <div class="calorie-badge" style="left:675px; top:520px;">
      <div class="count">50</div>
      <div class="unit">Calorie<br>per bottle</div>
    </div>
    <div class="volume" style="left:572px; top:576px;">500 ML</div>

    <div class="facts-title" style="left:895px; top:60px;">NUTRITIONAL FACTS</div>
    <div class="facts-panel" style="left:843px; top:88px;">
      <div class="row"><span>Serving Size</span><span>500 ML</span></div>
      <div class="row thick"><span>Servings Per Container</span><span>1</span></div>
      <div class="row thick"><span>Amount Per Serving</span><span>Calories 50</span></div>
      <div class="row right"><span>% Daily Value</span></div>
      <div class="row"><span>Fat</span><span>0g [0%]</span></div>
      <div class="row"><span>Sodium</span><span>1.28g [53%]</span></div>
      <div class="row"><span>Total Carbohydrate</span><span>9.6g [3.2%]</span></div>
      <div class="row"><span>Sugar</span><span>9.6g</span></div>
      <div class="row thick"><span>Protein</span><span>0g</span></div>
      <div class="vit head"><span></span><span>Per Serving</span><span>Per Bottle</span></div>
      <div class="vit"><span>Vitamin C</span><span>18.3%</span><span>18.3%</span></div>
      <div class="vit"><span>Vitamin E</span><span>3.5%</span><span>3.5%</span></div>
      <div class="vit"><span>Vitamin B3</span><span>3.0%</span><span>3.0%</span></div>
      <div class="vit"><span>Vitamin B5</span><span>3.0%</span><span>3.0%</span></div>
      <div class="vit"><span>Vitamin B6</span><span>5.5%</span><span>5.5%</span></div>
      <div class="vit"><span>Vitamin B12</span><span>2.3%</span><span>2.3%</span></div>
      <div class="vit"><span>Calcium</span><span>2.7%</span><span>2.7%</span></div>
      <div class="note">* Daily Value based on 2000 calorie diet</div>
      <div class="section">
        <strong>INGREDIENTS</strong>
        <p>Purified water, Sugar, Fructose, Favours, Colors, Food Acid (330) B3 Niacin, Pantothenic Acid, Vitamin B5, B6, B12, Calcium Lactate, Preservative (202)</p>
        <p>Manufactured Exclusively for Qirna Vitamin using imported ingredients in Malaysia.</p>
      </div>
      <div class="section">
        <em>A Prodoct of Qirna Vitamin</em>
        <em>Jeddah 21730 PO Box 4820, Saudi Arabia</em>
      </div>
      <div class="section" style="border-bottom:none;">
        <strong>For Sales &amp; Distribution Enquiries :</strong>
        info@qirnavitamin.com
      </div>
    </div>
  </section>

</body>
</html>
```